Brightwater Care Partners, LLC Business Card update!

would like a classier business card. Our cards currently just have our logo and contact information. Need better use of color and creativity
Logo attached.

Target Market(s)

Potential clients, contacts, existing clients. We are a consulting company

Industry/Entity Type

Business

Contact Information for Business Card

We like our colors but just have a boring card with our logo and a white background. I want something that stands out.

Colors
ec1f27
757575

Requirements
Must have
• Color to stay consistent. Logo provided
Nice to have
• Just better use of color/ design

```html
<!DOCTYPE html>
<html lang="en">
<head>
<meta charset="utf-8">
<title>Brightwater Care Partners — Business Card</title>
<link rel="stylesheet" href="https://fonts.googleapis.com/css2?family=Questrial&display=swap">
<style>
  :root {
    --brand-red: #c8161d;
    --brand-grey: #3c3c3c;
    --text-grey: #4a4a4a;
    --card-frost: #ebe8e4;
    --card-edge: #d6d2cc;
    --backdrop: #d9d4cd;
  }
  * { box-sizing: border-box; margin: 0; padding: 0; }
  html, body {
    width: 1200px;
    height: 970px;
    overflow: hidden;
    background: var(--backdrop);
    font-family: "Questrial", sans-serif;
  }
  .card {
    position: absolute;
    left: 100px;
    top: 207px;
    width: 1000px;
    height: 556px;
    background: var(--card-frost);
    border: 1px solid var(--card-edge);
  }
  .brand {
    position: absolute;
    left: 50px;
    top: 78px;
    display: flex;
    align-items: center;
    gap: 18px;
  }
  .brand-mark {
    width: 34px;
    height: 34px;
    background: var(--brand-red);
  }
  .brand-name {
    color: var(--brand-red);
    font-size: 40px;
    line-height: 1.05;
    font-weight: 400;
  }
  .holder {
    position: absolute;
    left: 48px;
    top: 290px;
  }
  .holder-name {
    color: var(--text-grey);
    font-size: 34px;
  }
  .holder-role {
    display: flex;
    align-items: center;
    margin-top: 10px;
    color: var(--brand-red);
    font-size: 22px;
  }
  .holder-role::after {
    content: "";
    display: block;
    width: 290px;
    height: 2px;
    margin-left: 4px;
    background: linear-gradient(to right, var(--brand-red), rgba(200,22,29,0.15));
  }
  .contacts {
    position: absolute;
    left: 48px;
    top: 428px;
    list-style: none;
  }
  .contacts li {
    display: flex;
    align-items: center;
    gap: 8px;
    color: var(--text-grey);
    font-size: 23px;
    line-height: 30px;
  }
  .contacts svg { width: 16px; height: 16px; fill: var(--brand-red); }
  .feature-brand {
    position: absolute;
    left: 560px;
    top: 130px;
    width: 420px;
    height: 424px;
    display: flex;
    align-items: center;
    justify-content: center;
    gap: 28px;
  }
  .feature-mark {
    flex: none;
    width: 110px;
    height: 110px;
    background: var(--brand-red);
  }
  .feature-name {
    color: var(--brand-grey);
    font-size: 50px;
    line-height: 1.1;
  }
</style>
</head>
<body>
  <main class="card">
    <div class="brand">
      <span class="brand-mark"></span>
      <div class="brand-name">Brightwater<br>Care Partners</div>
    </div>

    <div class="holder">
      <p class="holder-name">Daniel Mercer</p>
      <p class="holder-role">CEO</p>
    </div>

    <ul class="contacts">
      <li>
        <svg viewBox="0 0 16 16" aria-hidden="true"><path d="M3 1l3 3-2 2c1 2 3 4 5 5l2-2 3 3-2 3C6 15 1 10 1 3z"/></svg>
        + 999 999 9999
      </li>
      <li>
        <svg viewBox="0 0 16 16" aria-hidden="true"><path d="M1 3h14v10H1z M1 3l7 6 7-6" /></svg>
        info@brightwatercp.com
      </li>
      <li>
        <svg viewBox="0 0 16 16" aria-hidden="true"><circle cx="8" cy="8" r="7"/><path d="M1 8h14M8 1v14" stroke="#ebe8e4" stroke-width="1.2" fill="none"/></svg>
        www.brightwatercp.com
      </li>
    </ul>

    <div class="feature-brand">
      <span class="feature-mark"></span>
      <p class="feature-name">Brightwater<br>Care<br>Partners</p>
    </div>
  </main>
</body>
</html>
```